Moravel Aesthetic Doctor

I require an elegant, luxurious looking business card for my aesthetic business. I am a doctor and that will set me aside from competitors. I am planning to provide home and spa based treatments to clients with high expectations. I have attached my logo.

```html
<!DOCTYPE html>
<html lang="en">
<head>
<meta charset="utf-8">
<title>Moravel Aesthetic Doctor – Business Card</title>
<link rel="stylesheet" href="https://fonts.googleapis.com/css2?family=Lato:wght@400;700&display=swap">
<style>
  :root {
    --backdrop: #e8e8e8;
    --card-white: #ffffff;
    --card-grey: #999999;
    --accent-blue: #7ecbea;
    --text-grey: #8e8f93;
    --text-white: #ffffff;
    --band-grey: #999999;
  }
  * { margin: 0; padding: 0; box-sizing: border-box; }
  html, body {
    width: 1200px; height: 1200px; overflow: hidden;
    background: var(--backdrop);
    font-family: "Lato", sans-serif;
  }
  .card {
    position: absolute; width: 830px; height: 478px;
    box-shadow: 0 3px 10px rgba(0,0,0,0.35);
    overflow: hidden;
  }
  .card--front { left: 189px; top: 83px; background: var(--card-white); }
  .card--back { left: 186px; top: 647px; background: var(--card-grey); }

  .brand { position: absolute; left: 34px; top: 188px; display: flex; align-items: center; gap: 14px; }
  .brand__mark { width: 96px; height: 96px; border-radius: 50%; border: 3px solid var(--text-grey); flex: none; }
  .brand__name {
    font-weight: 400; font-size: 42px; letter-spacing: 3px; line-height: 1.05;
    color: var(--text-grey); text-transform: uppercase;
  }
  .brand__name small { display: block; font-size: 21px; letter-spacing: 2.4px; }
  .card--back .brand__mark { border-color: var(--text-white); }
  .card--back .brand__name { color: var(--text-white); }

  .divider { position: absolute; left: 414px; top: 165px; width: 2px; height: 150px; background: var(--accent-blue); }

  .details { position: absolute; left: 454px; top: 160px; color: var(--text-grey); }
  .details__name { font-size: 22px; line-height: 1.2; }
  .details__name strong { color: var(--accent-blue); font-weight: 700; }
  .details__title { font-size: 16.5px; margin-top: 8px; }
  .contacts { list-style: none; margin-top: 18px; }
  .contacts li { display: flex; align-items: center; gap: 10px; font-size: 21px; height: 29px; }
  .contacts svg { width: 19px; height: 19px; flex: none; }
  .social { display: inline-block; width: 16px; height: 16px; border-radius: 50%; background: var(--accent-blue); margin-left: 4px; }

  .band-blue { position: absolute; left: 0; bottom: 0; width: 420px; height: 20px; background: var(--accent-blue); clip-path: polygon(0 0, 100% 0, 94% 100%, 0 100%); }
  .band-grey { position: absolute; right: 0; bottom: 0; width: 422px; height: 46px; background: var(--band-grey); clip-path: polygon(42px 0, 100% 0, 100% 100%, 0 100%); }
  .band-grey__text { position: absolute; right: 40px; bottom: 0; height: 46px; line-height: 46px; color: var(--text-white); font-size: 20.5px; }

  .services { position: absolute; left: 459px; top: 153px; list-style: none; color: var(--text-white); }
  .services li { font-size: 22px; height: 28.2px; line-height: 28px; display: flex; align-items: center; gap: 10px; }
  .services li::before { content: ""; width: 8px; height: 8px; border-radius: 50%; background: var(--accent-blue); flex: none; }
</style>
</head>
<body>
  <section class="card card--front">
    <div class="brand">
      <span class="brand__mark"></span>
      <div class="brand__name">Moravel<small>Aesthetic Doctor</small></div>
    </div>
    <div class="divider"></div>
    <div class="details">
      <p class="details__name"><strong>Dr Elin Varga,</strong> MRCPCH MD</p>
      <p class="details__title">Australasian Diploma of Aesthetic Medicine</p>
      <ul class="contacts">
        <li>
          <svg viewBox="0 0 20 20" aria-hidden="true"><path d="M5 2l3 3-2 2c1 2.5 3 4.5 5.5 5.5l2-2 3 3-2 2.5C9 16 4 11 2.5 5z" fill="var(--accent-blue)"/></svg>
          0800 555 019
        </li>
        <li>
          <svg viewBox="0 0 20 20" aria-hidden="true"><rect x="2" y="5" width="16" height="11" fill="var(--accent-blue)"/><path d="M2 5l8 6 8-6" stroke="#fff" stroke-width="1.5" fill="none"/></svg>
          elin@moravel.co.nz
        </li>
        <li>
          <svg viewBox="0 0 20 20" aria-hidden="true" fill="none" stroke="var(--accent-blue)" stroke-width="1.3"><circle cx="10" cy="10" r="8"/><ellipse cx="10" cy="10" rx="3.5" ry="8"/><path d="M2 10h16M3.5 6h13M3.5 14h13"/></svg>
          www.moravel.co.nz
          <span class="social"></span><span class="social"></span>
        </li>
      </ul>
    </div>
    <div class="band-blue"></div>
    <div class="band-grey"></div>
    <p class="band-grey__text">Home and Spa Based Treatments</p>
  </section>

  <section class="card card--back">
    <div class="brand">
      <span class="brand__mark"></span>
      <div class="brand__name">Moravel<small>Aesthetic Doctor</small></div>
    </div>
    <div class="divider"></div>
    <ul class="services">
      <li>Dermal injectables</li>
      <li>Plasma facials</li>
      <li>Microneedling</li>
      <li>Skin boosters</li>
      <li>Excessive sweating</li>
      <li>Home and Spa Based Treatments</li>
    </ul>
  </section>
</body>
</html>
```